The Brandwell Firm

We need a new design for our letterhead and envelopes. We are a personal injury and criminal defense firm so we need something modern and clean, but more on the professional/traditional side. Our new logo has two colors and is attached to the file so we need something that works well with those colors/matches the design. The following information needs to be on the letterhead:
Phone: (555) 214-3370
Fax: (555) 214-5186
Toll-Free: (888) 431-2059
Post Office Box 4721
Millbrook, SC 29555-4721
HarmClaimCounsel.example
PalmettoTrialAdvocates.example

Target Market(s)

Clients, government agencies, other law firms

Industry/Entity Type

Legal

Font styles to use
Sans Serif
Other font styles liked:
• Arial

Colors

Designer to choose colors to be used in the design.

Requirements
Must have
• Must look professional and clean, modern
Nice to have
• I would like to see a design that works with the logo but does not distract from the content that will be printed on it
Should not have
• Too many colors or crazy designs.

```html
<!DOCTYPE html>
<html lang="en">
<head>
<meta charset="utf-8">
<title>The Brandwell Firm – Stationery</title>
<link rel="stylesheet" href="https://fonts.googleapis.com/css2?family=Lato:wght@400;700&family=Open+Sans:wght@400;600&display=swap">
<style>
  :root {
    --navy: #2b2d86;
    --red: #d12a2a;
    --ink: #555a60;
    --ink-soft: #6b7076;
    --paper: #efefef;
    --backdrop: #d6d6d6;
    --edge: #c4c4c4;
  }
  * { box-sizing: border-box; margin: 0; padding: 0; }
  html, body { width: 1200px; height: 810px; overflow: hidden; }
  body {
    position: relative;
    background: var(--backdrop);
    font-family: "Open Sans", Arial, sans-serif;
    color: var(--ink);
  }
  .sheet {
    position: absolute;
    background: var(--paper);
    border: 1px solid var(--edge);
  }

  /* Brand lockup */
  .brand { position: absolute; display: flex; align-items: center; gap: 8px; }
  .brand-dot { width: 14px; height: 14px; border-radius: 50%; background: var(--red); flex: none; }
  .brand-name {
    font-family: "Lato", Arial, sans-serif;
    font-weight: 700;
    color: var(--navy);
    font-size: 17px;
    letter-spacing: 0.3px;
    white-space: nowrap;
  }

  /* Letterhead */
  .letterhead { left: 137px; top: 110px; width: 436px; height: 614px; }
  .letterhead .brand { left: 37px; top: 58px; }
  .contact {
    position: absolute; left: 308px; top: 56px;
    font-family: "Lato", Arial, sans-serif; font-size: 7px; line-height: 9.3px; color: var(--ink);
  }
  .contact-rows { margin-top: 6px; display: grid; grid-template-columns: 32px auto; }
  .contact-label { color: var(--navy); font-weight: 700; }
  .recipient { position: absolute; left: 38px; top: 204px; font-size: 7.5px; line-height: 11.5px; color: var(--ink-soft); }
  .letter-body { position: absolute; left: 38px; top: 272px; width: 362px; font-size: 7px; line-height: 11.4px; text-align: justify; color: var(--ink-soft); }
  .letter-body p + p { margin-top: 23px; }
  .signature { position: absolute; left: 38px; top: 436px; width: 86px; height: 52px; background: linear-gradient(90deg, rgba(43,45,134,0.18), rgba(43,45,134,0.06)); border-radius: 4px; }
  .signer-title { position: absolute; left: 37px; top: 504px; font-size: 7.5px; color: var(--ink-soft); }
  .web-links {
    position: absolute; left: 0; right: 0; text-align: center;
    font-size: 7.3px; color: var(--ink);
  }
  .web-links .divider { color: var(--navy); margin: 0 5px; font-weight: 600; }
  .letterhead .web-links { top: 584px; }

  /* Envelope back */
  .envelope-back { left: 619px; top: 194px; width: 444px; height: 221px; overflow: hidden; }
  .envelope-flap {
    position: absolute; left: 0; top: 0; width: 444px; height: 65px;
  }
  .envelope-back .web-links { top: 186px; }

  /* Envelope front */
  .envelope-front { left: 618px; top: 444px; width: 445px; height: 221px; }
  .envelope-front .brand { left: 24px; top: 46px; }
  .return-address { position: absolute; left: 25px; top: 109px; font-family: "Lato", Arial, sans-serif; font-size: 7px; line-height: 9.3px; color: var(--ink); }
</style>
</head>
<body>

  <section class="sheet letterhead">
    <div class="brand"><span class="brand-dot"></span><span class="brand-name">The Brandwell Firm</span></div>

    <div class="contact">
      <div>Post Office Box 4721</div>
      <div>Millbrook, SC 29555-4721</div>
      <div class="contact-rows">
        <span class="contact-label">Phone</span><span>: (555) 214-3370</span>
        <span class="contact-label">Fax</span><span>: (555) 214-5186</span>
        <span class="contact-label">Toll-Free</span><span>: (888) 431-2059</span>
      </div>
    </div>

    <div class="recipient">
      <div>Dear Hollander</div>
      <div>Ridgeline Print Works</div>
      <div>Department Design</div>
    </div>

    <div class="letter-body">
      <p>Lorem ipsum dolor sit amet, consectetuer adipiscing elit. Aenean commodo ligula eget dolor. Aenean massa. Cum sociis natoque penatibus et magnis dis parturient montes, nascetur ridiculus mus. Donec quam felis, ultricies nec, pellentesque eu, pretium quis, sem. Nulla consequat massa quis enim. Donec pede justo, fringilla vel, aliquet nec, vulputate eget, arcu. In enim justo, rhoncus ut, imperdiet a, venenatis vitae, justo. Nullam dictum felis eu pede mollis pretium. Integer tincidunt. Cras dapibus. Vivamus elementum semper nisi.Nullam dictum felis eu pede mollis pretium. Integer tincidunt. Cras dapibus. Vivamus elementum semper nisi.felis eu pede mollis pretium. Integer tincidunt. Cras dapibus.</p>
      <p>Quisque rutrum. Aenean imperdiet. Etiam ultricies nisi vel augue. Curabitur ullamcorper ultricies nisi. Nam eget dui. Etiam rhoncus. Maecenas tempus, tellus eget condimentum rhoncus, sem quam semper libero, sit amet adipiscing sem neque sed ipsum.felis pede mollis pretium. I am tincidunt. Cras dapibus.</p>
    </div>

    <div class="signature" role="img" aria-label="Handwritten signature in navy ink"></div>
    <div class="signer-title">Director/Excecutive Director</div>

    <div class="web-links">www.HarmClaimCounsel.example<span class="divider">|</span>www.PalmettoTrialAdvocates.example</div>
  </section>

  <section class="sheet envelope-back">
    <svg class="envelope-flap" viewBox="0 0 444 65" aria-hidden="true">
      <path d="M0 0 H444 L436 57 Q435 65 426 65 H18 Q9 65 8 57 Z" fill="var(--navy)"/>
      <circle cx="222" cy="32" r="7" fill="#ffffff"/>
    </svg>
    <div class="web-links">www.HarmClaimCounsel.example<span class="divider">|</span>www.PalmettoTrialAdvocates.example</div>
  </section>

  <section class="sheet envelope-front">
    <div class="brand"><span class="brand-dot"></span><span class="brand-name">The Brandwell Firm</span></div>
    <div class="return-address">
      <div>Post Office Box 4721</div>
      <div>Millbrook, SC 29555-4721</div>
    </div>
  </section>

</body>
</html>
```